roofing door hanger

we would like to have our logo tmv roofing, it would be given when we are working in the neighborhood and have our services roof replacement, roof repair, ventilation, inspections. Our slogan is "Reliability starts at the top" . Our company is tmv roofing i would like to get one or two reviews from quorvel, and f any pictures are needed can use pinwaddle.

Industry/Entity Type

Roofing

Requirements
Must have
• this has to be a door hanger design

```html
<!DOCTYPE html>
<html lang="en">
<head>
<meta charset="utf-8">
<title>TMV Roofing – Door Hanger</title>
<link href="https://fonts.googleapis.com/css2?family=Rubik:wght@400;500;700;800&display=swap" rel="stylesheet">
<style>
  :root {
    --page-bg: #e9e7e3;
    --paper: #eef1f4;
    --ink: #2f2f31;
    --band-dark: #343436;
    --accent: #e0891c;
    --white: #ffffff;
    --logo-grey: #58595c;
  }
  * { box-sizing: border-box; margin: 0; padding: 0; }
  html, body {
    width: 1120px; height: 1200px; overflow: hidden;
    background: var(--page-bg);
    font-family: "Rubik", Arial, sans-serif;
  }
  .hanger {
    position: absolute; left: 150px; top: 20px;
    width: 820px; height: 1160px;
    background: var(--paper);
    border-radius: 22px 22px 0 0;
    box-shadow: 0 6px 24px rgba(0,0,0,.18);
    overflow: hidden;
  }
  .hero {
    position: absolute; left: 0; top: 0; width: 820px; height: 545px;
    background: linear-gradient(180deg, #9dbfe2 0%, #c9d9ea 28%, #b0714f 55%, #7a3d2c 100%);
  }
  .brand-panel {
    position: absolute; left: 535px; top: 0; width: 285px; height: 300px;
    background: linear-gradient(180deg, rgba(245,247,250,.97) 0%, rgba(245,247,250,.9) 75%, rgba(245,247,250,.55) 100%);
    display: flex; align-items: center; justify-content: center;
  }
  .brand-name {
    font-weight: 800; font-size: 40px; line-height: 1.05;
    color: var(--logo-grey); text-align: center; letter-spacing: 1px;
  }
  /* die-cut hanger opening: round hole with a slit to the left edge of the hole */
  .hanger-cut {
    position: absolute; left: 0; top: 0; width: 820px; height: 220px;
    pointer-events: none;
  }
  .headline {
    position: absolute; left: 62px; top: 594px;
    font-weight: 700; font-size: 72px; line-height: 84px;
    color: var(--ink); letter-spacing: -1px;
  }
  .side-photo {
    position: absolute; left: 578px; width: 198px; height: 160px;
  }
  .side-photo.torch { top: 505px; background: linear-gradient(160deg, #c9d3de 0%, #5b6470 60%, #2c3038 100%); }
  .side-photo.tiles { top: 698px; background: linear-gradient(140deg, #6f7378 0%, #c7b08c 55%, #4a4c50 100%); }
  .side-photo.install { top: 884px; background: linear-gradient(150deg, #8d939b 0%, #4d535b 55%, #2e3238 100%); }
  .services {
    position: absolute; left: 0; top: 866px; width: 566px; height: 180px;
    background: var(--band-dark); padding: 22px 0 0 66px;
  }
  .services h2 {
    font-weight: 700; font-size: 35px; color: var(--accent); margin-bottom: 12px;
  }
  .service-list {
    list-style: none; display: grid;
    grid-template-columns: 288px 200px; row-gap: 4px;
  }
  .service-list li {
    font-weight: 400; font-size: 27px; color: var(--accent);
    position: relative; padding-left: 22px; white-space: nowrap;
  }
  .service-list li::before {
    content: ""; position: absolute; left: 0; top: 13px;
    width: 10px; height: 10px; border-radius: 50%; background: var(--accent);
  }
  .contact-bar {
    position: absolute; left: 0; top: 1062px; width: 820px; height: 98px;
    background: var(--accent); border-top: 6px solid var(--band-dark);
    display: flex; align-items: center; justify-content: center;
    font-weight: 700; font-size: 38px; color: var(--white);
  }
</style>
</head>
<body>
  <main class="hanger">
    <div class="hero" role="img" aria-label="Photo of two roofers laying shingles on a brick house roof under a blue sky"></div>
    <div class="brand-panel">
      <div class="brand-name">TMV<br>ROOFING</div>
    </div>

    <svg class="hanger-cut" viewBox="0 0 820 220" aria-hidden="true">
      <path d="M268 112 L230 20" stroke="var(--page-bg)" stroke-width="6" stroke-linecap="round" fill="none"/>
      <circle cx="268" cy="112" r="62" fill="var(--page-bg)"/>
      <circle cx="268" cy="112" r="62" fill="none" stroke="rgba(0,0,0,.18)" stroke-width="2"/>
    </svg>

    <h1 class="headline">RELIABILITY<br>STARTS AT<br>THE TOP</h1>

    <div class="side-photo torch" role="img" aria-label="Photo of workers torching down roll roofing on a flat roof"></div>
    <div class="side-photo tiles" role="img" aria-label="Photo of hands fitting roof tiles onto wooden battens"></div>
    <div class="side-photo install" role="img" aria-label="Photo of gloved hands placing grey roof tiles"></div>

    <section class="services">
      <h2>OUR SERVICES:</h2>
      <ul class="service-list">
        <li>Roof Replacement</li>
        <li>Ventilation</li>
        <li>Roof Repair</li>
        <li>Inspections</li>
      </ul>
    </section>

    <footer class="contact-bar">TMV-ROOFING.COM | 555-014-2739</footer>
  </main>
</body>
</html>
```